Commercial/Corporate Law Firm needs Website Design

Hi guys. I've started up a new law firm and would love your help designing an attractive website. I'll need both design and coding, and to make it easy for us to edit as necessary later, I think it should be built off a Wordpress.org structure.
FIRST IMPRESSIONS
It's very important that the first impression of the website really captures our prospective clients' attention and impresses them. Their first three seconds needs to be good.
I imagine the homepage may be short, with a menu bar and a compelling image, and with a tagline overlaid or underneath (eg. "It's about results.")
The image should be related to our practice areas: eg. IPOs, corporate transactions, or commercial negotiations.
I have previously suggested there could be a skyline image of Sydney or Adelaide. However, because we are based in Adelaide, I don't think Sydney is appropriate - and Adelaide is probably too boring to use.
HOMEPAGE
Being a new firm, we don't have many existing testimonials, and I will be the only lawyer to start with. So we need to focus on the nature of the services we will provide and how my experience can help them. We have an existing logo to use, and I would like the website colour scheme not to clash with that logo (dark blue and white).
After the initial image and tagline there should be a brief introduction to each of the main areas of work, eg. "We specialise in three main areas of practice:"
1. Corporate Transactions and Regulation
2. Business Law and Dispute Resolution
3. Migration Assistance
These should each have an appropriate photo and link to a separate page that briefly describes our services in that area.
Below that there should be a message from me with a photo. Finally, at the bottom, there should be a "Contact Us" section which shows a Google image of our address, contact details, and then our logo with colours inverted.
OTHER PAGES
While we will need some other pages, they should all be fairly simple. I think we will need one page to say "About Us", where I will put information about my experience. I think we will then need one page for each of the 3 areas listed above, which just needs an appropriate image and then text to describe the service. Finally, a "Contact Us" page which I imagine will be the same as the bottom of the homepage.
OTHER DETAILS
For now you can use details from my LinkedIn page to fill out any other text as necessary, or the photo.
Because the logo is square, I would prefer the design of the website also to be rectangular.
Looking forward to seeing your work! Thank you.
Marcus
Potential clients:
Businesses with legal issues or disputes
Companies wishing to list on the stock market

```html
<!DOCTYPE html>
<html lang="en">
<head>
<meta charset="utf-8">
<title>Corvell Legal</title>
<link href="https://fonts.googleapis.com/css2?family=Tinos:ital,wght@0,400;0,700;1,400&family=Arimo:ital,wght@0,400;0,700;1,400&family=Open+Sans:wght@400;600&display=swap" rel="stylesheet">
<style>
:root{
  --navy:#1b3766;
  --ink:#1f2d4a;
  --text:#4a4a4a;
  --muted:#6d6d6d;
  --white:#ffffff;
  --rule:#8f8f8f;
  --footer:#6b6b6b;
  --hero-a:#3f5680;
  --hero-b:#7d8fae;
}
*{margin:0;padding:0;box-sizing:border-box}
html,body{width:1200px;height:2941px;overflow:hidden;background:var(--white)}
body{position:relative;font-family:"Arimo",Arial,sans-serif;color:var(--text)}
.abs{position:absolute}
.serif{font-family:"Tinos","Times New Roman",serif;font-weight:400}

/* header */
.site-header{left:0;top:0;width:1200px;height:145px;background:var(--white)}
.brand{left:78px;top:14px;width:200px;height:120px;text-align:center}
.brand-square{display:block;margin:0 auto 8px;width:62px;height:62px;background:var(--navy)}
.brand-name{font-family:"Tinos",serif;font-size:29px;letter-spacing:1px;color:var(--navy);line-height:1;white-space:nowrap}
.nav{left:633px;top:60px;height:36px;display:flex;align-items:center;font-size:12.5px;color:var(--ink)}
.nav a{color:var(--ink);text-decoration:none;margin-right:56px}
.nav a.active{background:var(--navy);color:var(--white);width:103px;height:36px;display:flex;align-items:center;justify-content:center;outline:1px solid var(--navy);outline-offset:2px;margin-right:62px}

/* hero */
.hero{left:0;top:145px;width:1200px;height:575px;background:linear-gradient(115deg,#2a3d63 0%,var(--hero-a) 35%,var(--hero-b) 62%,#4d6088 100%)}
.hero-title{left:0;top:186px;width:1200px;text-align:center;color:var(--white);font-size:44px}
.hero-sub{left:0;top:272px;width:1200px;text-align:center;color:var(--white);font-style:italic;font-size:15px}
.btn-outline{border:2px solid var(--white);color:var(--white);display:flex;align-items:center;justify-content:center;font-size:21px}
.hero-cta{left:525px;top:333px;width:150px;height:48px;background:rgba(27,55,102,.55)}
.hero-arrow{top:261px;width:54px;height:52px;border:2px solid var(--white);display:flex;align-items:center;justify-content:center}

/* info band */
.info-band{left:0;top:720px;width:1200px;height:113px;background:var(--navy)}
.info-item{top:20px;display:flex;color:var(--white)}
.info-icon{width:62px;height:62px;border:2px solid var(--white);display:flex;align-items:center;justify-content:center;margin-right:14px;flex:none}
.info-item h3{font-weight:400;font-size:17px;margin-bottom:6px}
.info-item p{font-size:13px;line-height:25px;width:200px}

/* about */
.about-frame{left:560px;top:898px;width:542px;height:413px;border:1px solid #6f7a8c}
.about-photo{left:562px;top:895px;width:560px;height:418px;background:linear-gradient(135deg,#c9c9c7,#8e939b 55%,#e3e2de)}
.about-card{left:88px;top:912px;width:534px;height:380px;background:var(--white);box-shadow:0 0 12px rgba(0,0,0,.28);padding:68px 36px 0 36px}
.section-title{font-size:34px;color:var(--ink)}
.section-title .lead{color:var(--navy)}
.divider{display:flex;align-items:center;gap:14px;margin:10px 0 18px}
.divider span{display:block;width:52px;height:1px;background:var(--rule)}
.about-card p{font-family:"Open Sans",sans-serif;font-size:13.5px;line-height:26px;width:388px;color:var(--text)}
.btn-solid{background:var(--navy);color:var(--white);display:flex;align-items:center;justify-content:center;outline:2px solid var(--navy);outline-offset:2px;border:1px solid var(--white)}
.about-btn{margin-top:20px;width:131px;height:38px;font-size:18px}

/* practice */
.practice{left:0;top:1375px;width:1200px;height:635px;background:linear-gradient(100deg,#39486a 0%,#5d6b88 45%,#3d4b6b 100%)}
.practice-title{left:0;top:58px;width:1200px;text-align:center;color:var(--white);font-size:34px}
.practice-divider{left:0;top:118px;width:1200px;display:flex;justify-content:center;align-items:center;gap:14px}
.practice-divider span{display:block;width:52px;height:1px;background:var(--white)}
.card{top:150px;width:323px;height:423px;background:var(--white);text-align:center}
.card-photo{position:absolute;left:5px;width:313px;height:190px}
.card h3{font-weight:400;font-size:17.5px;line-height:29px;color:var(--navy)}
.card p{font-family:"Open Sans",sans-serif;font-size:12.5px;line-height:25px;color:var(--muted);width:260px;margin:8px auto 0}
.card .btn-solid{width:135px;height:38px;margin:14px auto 0;font-size:16px}

/* contact */
.contact-photo{left:78px;top:2068px;width:382px;height:444px;background:linear-gradient(180deg,#f2f2f2 0%,#e8e5e3 40%,#2e3447 75%,#262b3c 100%)}
.contact-title{left:467px;top:2068px}
.field{border:1px solid #e2e2e2;box-shadow:0 1px 5px rgba(0,0,0,.2);background:var(--white);font-size:13px;color:var(--text);padding:17px 14px}
.submit{left:465px;top:2398px;width:657px;height:52px;font-size:18px}

/* contact bar */
.contact-bar{left:78px;top:2512px;width:1044px;height:104px;background:var(--navy)}
.social{top:30px;width:40px;height:40px;border:2px solid var(--white)}
.bar-item{top:26px;color:var(--white);display:flex;gap:14px}
.bar-item h4{font-weight:400;font-size:17px;margin-bottom:6px}
.bar-item p{font-size:14px}

/* footer */
.footer{left:0;top:2565px;width:1200px;height:376px;background:var(--footer)}
.footer-brand{left:78px;top:80px;width:232px;text-align:center;color:var(--white)}
.footer-brand .brand-square{background:var(--white);width:62px;height:62px;margin-bottom:10px}
.footer-brand .brand-name{color:var(--white)}
.footer-brand p{font-size:13.5px;line-height:25px;margin:14px auto 0;width:212px}
.footer-col{top:84px;color:var(--white)}
.footer-col h4{font-weight:400;font-size:18px;margin-bottom:14px}
.footer-col ul{list-style:none}
.footer-col li{font-size:13.5px;line-height:25px;margin-bottom:16px;padding-left:32px;position:relative}
.footer-col li::before{content:"";position:absolute;left:0;top:8px;border-left:7px solid var(--white);border-top:5px solid transparent;border-bottom:5px solid transparent}
.footer-col p{font-size:13.5px;line-height:25px;width:205px}
.newsletter{top:220px;width:236px;height:52px;display:flex}
.newsletter span{flex:1;background:var(--white);font-size:13px;color:#333;padding:18px 12px}
.newsletter b{width:52px;background:var(--navy);display:flex;align-items:center;justify-content:center}
.footer-rule{left:78px;top:320px;width:1044px;height:1px;background:#9a9a9a}
.copyright{left:0;top:342px;width:1200px;text-align:center;color:var(--white);font-size:14px}
</style>
</head>
<body>

<header class="site-header abs">
  <div class="brand abs">
    <span class="brand-square"></span>
    <div class="brand-name">CORVELL LEGAL</div>
  </div>
  <nav class="nav abs">
    <a class="active" href="#">Home</a>
    <a href="#">About Us</a>
    <a href="#">Practice Areas</a>
    <a href="#">Contact Us</a>
  </nav>
</header>

<section class="hero abs" role="img" aria-label="Lawyer stamping a document beside a figure of Lady Justice">
  <h1 class="hero-title abs serif">WE GET RESULTS</h1>
  <p class="hero-sub abs">Lorem Ipsum is simply dummy text of the printing and</p>
  <div class="hero-cta abs btn-outline">CONTACT US</div>
  <div class="hero-arrow abs" style="left:14px">
    <svg width="26" height="22" viewBox="0 0 26 22" fill="none" stroke="#fff" stroke-width="2.5"><path d="M12 2 3 11l9 9M23 2l-9 9 9 9"/></svg>
  </div>
  <div class="hero-arrow abs" style="left:1136px">
    <svg width="26" height="22" viewBox="0 0 26 22" fill="none" stroke="#fff" stroke-width="2.5"><path d="M3 2l9 9-9 9M14 2l9 9-9 9"/></svg>
  </div>
</section>

<section class="info-band abs">
  <div class="info-item abs" style="left:78px">
    <div class="info-icon"><svg width="28" height="20" viewBox="0 0 28 20"><rect x="1" y="1" width="26" height="18" fill="#fff"/><path d="M1 1l13 10L27 1" fill="none" stroke="#1b3766" stroke-width="2"/></svg></div>
    <div><h3>Case Evaluation</h3><p>Lorem Ipsum is simply dummy text of the printing and</p></div>
  </div>
  <div class="info-item abs" style="left:440px">
    <div class="info-icon"><svg width="22" height="30" viewBox="0 0 22 30"><path d="M11 1C5.5 1 1 5.3 1 10.8 1 18 11 29 11 29s10-11 10-18.2C21 5.3 16.5 1 11 1z" fill="none" stroke="#fff" stroke-width="2.5"/><circle cx="11" cy="11" r="3.5" fill="#fff"/></svg></div>
    <div><h3>Office Location</h3><p>123, Lorem Ipsum is simply dummy text of the</p></div>
  </div>
  <div class="info-item abs" style="left:800px">
    <div class="info-icon"><svg width="26" height="28" viewBox="0 0 26 28" fill="#fff"><circle cx="13" cy="8" r="7"/><path d="M0 28c0-8 6-12 13-12s13 4 13 12z"/></svg></div>
    <div><h3>Free Consultation</h3><p>Lorem Ipsum is simply dummy text of the printing and</p></div>
  </div>
</section>

<div class="about-frame abs"></div>
<div class="about-photo abs" role="img" aria-label="Two lawyers in suits seated together in an office"></div>
<section class="about-card abs">
  <h2 class="section-title serif"><span class="lead">About</span> Us</h2>
  <div class="divider"><span></span><span></span></div>
  <p>Lorem Ipsum is simply dummy text of the printing and typesetting industry. Lorem Ipsum has been the industry's standard dummy text ever since the 1500s, when an unknown printer took a galley of type</p>
  <div class="btn-solid about-btn">READ MORE</div>
</section>

<section class="practice abs" role="img" aria-label="Blurred office with a Lady Justice statue">
  <h2 class="practice-title abs serif">Practice Areas</h2>
  <div class="practice-divider abs"><span></span><span></span></div>

  <article class="card abs" style="left:78px">
    <div class="card-photo" style="top:5px;background:linear-gradient(135deg,#8d7a6a,#d9d4cc 55%,#b6a99b)" role="img" aria-label="Team reviewing financial charts on a desk"></div>
    <div style="padding-top:208px">
      <h3>Corporate Transactions and<br>Regulation</h3>
      <p>Lorem Ipsum is simply dummy text of the printing and typesetting industry. Lorem Ipsum has been</p>
      <div class="btn-solid">READ MORE</div>
    </div>
  </article>

  <article class="card abs" style="left:438px">
    <div style="padding-top:16px">
      <h3>Business Law and Dispute<br>Resolution</h3>
      <p>Lorem Ipsum is simply dummy text of the printing and typesetting industry. Lorem Ipsum has been</p>
      <div class="btn-solid">READ MORE</div>
    </div>
    <div class="card-photo" style="top:228px;background:linear-gradient(135deg,#2c2c30,#b9bcc0 55%,#ededed)" role="img" aria-label="Handshake over a signed contract"></div>
  </article>

  <article class="card abs" style="left:800px">
    <div class="card-photo" style="top:5px;background:linear-gradient(135deg,#1f1f22,#d6d8dc 50%,#f2f2f2)" role="img" aria-label="Person working with a calculator and paperwork"></div>
    <div style="padding-top:208px">
      <h3>Migration Assistance</h3>
      <p style="margin-top:22px">Lorem Ipsum is simply dummy text of the printing and typesetting industry. Lorem Ipsum has been</p>
      <div class="btn-solid">READ MORE</div>
    </div>
  </article>
</section>

<div class="contact-photo abs" role="img" aria-label="Portrait of the principal lawyer in a dark suit"></div>
<div class="contact-title abs">
  <h2 class="section-title serif"><span class="lead">Contact</span> Us</h2>
  <div class="divider"><span></span><span></span></div>
</div>
<div class="field abs" style="left:465px;top:2158px;width:325px;height:55px">Name</div>
<div class="field abs" style="left:797px;top:2158px;width:325px;height:55px">E-mail</div>
<div class="field abs" style="left:465px;top:2220px;width:325px;height:55px">Phone</div>
<div class="field abs" style="left:797px;top:2220px;width:325px;height:55px">Subject</div>
<div class="field abs" style="left:465px;top:2283px;width:657px;height:107px">Message</div>
<div class="submit abs btn-solid">SUBMIT</div>

<footer class="footer abs">
  <div class="footer-brand abs">
    <span class="brand-square"></span>
    <div class="brand-name">CORVELL LEGAL</div>
    <p>Lorem Ipsum is simply dummy text of the printing and typesetting industry.</p>
  </div>
  <div class="footer-col abs" style="left:349px">
    <h4>QUICK LINKS</h4>
    <ul><li>Home</li><li>About us</li><li>Practice Areas</li><li>Contact Us</li></ul>
  </div>
  <div class="footer-col abs" style="left:619px">
    <h4>PRACTICE AREAS</h4>
    <ul><li>Corporate Transactions and<br>Regulation</li><li>Business Law and Dispute<br>Resolution</li><li>Migration Assistance</li></ul>
  </div>
  <div class="footer-col abs" style="left:890px">
    <h4>NEWSLETTER</h4>
    <p>Lorem Ipsum is simply dummy text of the printing and typesetting industry.</p>
  </div>
  <div class="newsletter abs" style="left:888px"><span>Enter E-mail</span><b><svg width="24" height="20" viewBox="0 0 24 20" fill="#fff"><path d="M0 0l24 10L0 20l3-10z"/></svg></b></div>
  <div class="footer-rule abs"></div>
  <p class="copyright abs">©CORVELL LEGAL - 2018. All Rights Reserved.</p>
</footer>

<section class="contact-bar abs">
  <span class="social abs" style="left:32px"></span>
  <span class="social abs" style="left:84px"></span>
  <span class="social abs" style="left:136px"></span>
  <span class="social abs" style="left:188px"></span>
  <span class="social abs" style="left:240px"></span>
  <div class="bar-item abs" style="left:622px">
    <svg width="24" height="18" viewBox="0 0 24 18" style="margin-top:3px"><rect width="24" height="18" fill="#fff"/><path d="M0 0l12 9L24 0" fill="none" stroke="#1b3766" stroke-width="2"/></svg>
    <div><h4>E-mail</h4><p>info@corvelllegal.com</p></div>
  </div>
  <div class="bar-item abs" style="left:866px">
    <svg width="22" height="22" viewBox="0 0 24 24" fill="#fff"><path d="M6.6 10.8a15.1 15.1 0 0 0 6.6 6.6l2.2-2.2c.3-.3.7-.4 1-.2 1.1.4 2.3.6 3.6.6.6 0 1 .4 1 1V20c0 .6-.4 1-1 1A17 17 0 0 1 3 4c0-.6.4-1 1-1h3.5c.6 0 1 .4 1 1 0 1.3.2 2.5.6 3.6.1.3 0 .7-.2 1z"/></svg>
    <div><h4>Phone</h4><p>555 014 2290</p></div>
  </div>
</section>

</body>
</html>
```